food delivery web site design

Currently we have a smartphone app (ios/android) that is being used by our clients to make orders to about 30 different restaurants.

We would like to extent this and have also a website that is able to mimic the same functionalities:
- register
- show restaurants based on the selected address
- make order to an restaurant
- being able to process orders for other registered users (please read the attached doc for complete info on this)

Take a look at the attached doc for more info.

```html
<!DOCTYPE html>
<html lang="ro">
<head>
<meta charset="utf-8">
<title>Gustio – Înregistrare</title>
<link href="https://fonts.googleapis.com/css2?family=Bebas+Neue&family=Oswald:wght@400;500&family=Open+Sans:wght@400&display=swap" rel="stylesheet">
<style>
  :root {
    --brand-red: #9b1a0d;
    --brand-red-light: #c0392b;
    --shield-brown: #2a1f1e;
    --accent-yellow: #f6cf5a;
    --pattern-light: #ececec;
    --footer-dark: #222222;
    --title-grey: #c9c9c9;
    --label-grey: #6b6b6b;
    --field-border: #cfcfcf;
    --footer-text: #e8e8e8;
    --white: #ffffff;
  }
  * { box-sizing: border-box; margin: 0; padding: 0; }
  html, body { width: 1200px; height: 831px; overflow: hidden; background: var(--white); }
  .page { position: relative; width: 1200px; height: 831px; }

  .top-pattern { position: absolute; left: 0; top: 0; width: 1200px; height: 50px;
    background: linear-gradient(180deg, #f4f4f4, var(--pattern-light)); }
  .nav-bar { position: absolute; left: 0; top: 50px; width: 1200px; height: 53px;
    background: var(--brand-red);
    border-top: 2px solid var(--brand-red-light);
    box-shadow: inset 0 -3px 0 #7e1409, 0 2px 0 var(--brand-red); }
  .rule { position: absolute; height: 3px; border-top: 1px solid rgba(255,255,255,.55); border-bottom: 1px solid rgba(255,255,255,.55); top: 27px; }
  .rule--left { left: 305px; width: 28px; }
  .rule--right { left: 1064px; width: 136px; }
  .rule--dotted { left: 610px; width: 277px; border-style: dotted; }

  .call-us { position: absolute; left: 350px; top: 10px; font-family: "Oswald", sans-serif; font-weight: 500;
    font-size: 24px; color: var(--white); letter-spacing: -0.3px; display: flex; align-items: center; gap: 6px; }
  .call-us__number { color: var(--accent-yellow); display: flex; align-items: center; gap: 4px; }

  .account-links { position: absolute; top: 14px; left: 906px; display: flex; gap: 22px;
    font-family: "Oswald", sans-serif; font-size: 15px; color: var(--white); }
  .account-links span { display: flex; align-items: center; gap: 6px; }

  .brand-shield { position: absolute; left: 138px; top: 0; width: 159px; height: 160px; }
  .brand-name { position: absolute; left: 163px; top: 58px; width: 110px; text-align: center;
    font-family: "Oswald", sans-serif; font-weight: 500; font-size: 26px; color: var(--brand-red); }

  .register { position: absolute; left: 138px; top: 225px; width: 924px; }
  .register__title { font-family: "Bebas Neue", sans-serif; font-weight: 400; font-size: 58px; line-height: 1;
    color: var(--title-grey); padding-bottom: 13px; border-bottom: 1px solid var(--field-border); }
  .field { margin-top: 37px; }
  .field + .field { margin-top: 44px; }
  .field__label { display: block; font-family: "Bebas Neue", sans-serif; font-size: 23px; color: var(--label-grey); line-height: 1; margin-bottom: 6px; }
  .field__input { width: 250px; height: 41px; border: 1px solid var(--field-border); background: var(--white); display: flex; }
  .field__prefix { width: 31px; border-right: 1px solid var(--field-border); display: flex; align-items: center; justify-content: center; }
  .submit { margin-top: 45px; width: 288px; height: 42px; background: var(--brand-red); color: var(--white); border: none;
    font-family: "Oswald", sans-serif; font-size: 18px; letter-spacing: -0.2px; }

  .site-footer { position: absolute; left: 0; top: 775px; width: 1200px; height: 56px; background: var(--footer-dark); }
  .footer-links { position: absolute; left: 138px; top: 19px; display: flex; font-family: "Open Sans", sans-serif; font-size: 12.5px; color: var(--footer-text); }
  .footer-links span + span { border-left: 1px solid #555; padding-left: 9px; margin-left: 9px; }
  .copyright { position: absolute; right: 140px; top: 19px; font-family: "Open Sans", sans-serif; font-size: 12.5px; color: var(--footer-text); }
</style>
</head>
<body>
<div class="page">
  <div class="top-pattern" role="img" aria-label="Decorative band of line-drawn food doodles"></div>

  <header class="nav-bar">
    <div class="rule rule--left"></div>
    <div class="call-us">SUNĂ-NE LA
      <span class="call-us__number">
        <svg width="16" height="20" viewBox="0 0 16 20"><path d="M3 1 L6 1 L7 6 L5 8 Q7 13 11 15 L13 13 L15 17 L13 19 Q4 17 1 5 Z" fill="var(--accent-yellow)"/></svg>
        0700 123 456</span>
    </div>
    <div class="rule rule--dotted"></div>
    <nav class="account-links">
      <span><svg width="14" height="12" viewBox="0 0 14 12"><path d="M1 12 Q1 5 8 5 L8 1 L14 6 L8 11 L8 8 Q3 8 1 12Z" fill="#fff"/></svg>LOGIN</span>
      <span><svg width="16" height="12" viewBox="0 0 16 12"><circle cx="6" cy="3.5" r="3" fill="#fff"/><path d="M0 12 Q0 7 6 7 Q12 7 12 12Z" fill="#fff"/><path d="M13 1v5M10.5 3.5h5" stroke="#fff" stroke-width="1.6"/></svg>SIGN IN</span>
    </nav>
    <div class="rule rule--right"></div>
  </header>

  <svg class="brand-shield" viewBox="0 0 159 160" aria-hidden="true">
    <polygon points="0,0 159,0 159,135 137,157 22,157 0,135" fill="var(--shield-brown)"/>
    <polyline points="6,0 6,132 25,151 134,151 153,132 153,0" fill="none" stroke="#6b5a58" stroke-width="1"/>
    <circle cx="80" cy="78" r="55" fill="var(--white)"/>
  </svg>
  <div class="brand-name">Gustio</div>

  <main class="register">
    <h1 class="register__title">Înregistrare</h1>
    <div class="field"><label class="field__label">Nume</label><div class="field__input"></div></div>
    <div class="field"><label class="field__label">Prenume</label><div class="field__input"></div></div>
    <div class="field"><label class="field__label">Telefon</label>
      <div class="field__input"><span class="field__prefix">
        <svg width="12" height="22" viewBox="0 0 12 22"><rect x="1" y="1" width="10" height="20" rx="2" fill="none" stroke="#aaa" stroke-width="1.4"/><line x1="1" y1="17" x2="11" y2="17" stroke="#aaa"/></svg>
      </span></div>
    </div>
    <button class="submit">TRIMITE-MI CODUL DE ÎNREGISTRARE</button>
  </main>

  <footer class="site-footer" role="img" aria-label="Dark footer band with faint food doodle pattern">
    <div class="footer-links"><span>Contactează-ne</span><span>Despre noi</span><span>Partenerii noștri</span><span>FAQ</span><span>Devino partener</span></div>
    <div class="copyright">Copyright © 2013 gustio.ro. Toate drepturile rezervate.</div>
  </footer>
</div>
</body>
</html>
```